"Copper Lantern" Play - Poster Design for Theatre Group

We are an amateur theatre group based in Geneva, Switzerland. We take pride in eye-catching posters for our shows, which are printed in various sizes.
This design will be for a play in March 2016. The play is called "Copper Lantern", and it's a Marwick Medal winner from Martin Crowe-Fenwick. The play is about a couple who have everything a family could want, until they lose a child in a life-shattering accident that turns their world upside down. The play charts the couple's bittersweet search to find each other and to find comfort.
Most importantly, we want a design that will make people want to see the show. We don't want to give away the plot or be too heavy-handed about death, but we want it to be clear that it's not a comedy (although there are some lighter moments!).
Attached you will find a template for the poster. This simply has our group name and logo in the top right corner: (Lakeside Stage Players Guild presents).
You may change the color of both the text and the logo, but please do not change the font, size, or location.
Here is the information that needs to be on the poster, wherever you see fit:
play title: Copper Lantern
author byline: by Martin Crowe-Fenwick
director line: directed by Ned Pilbury
tagline: How do you keep it together when your whole world's fallen apart?
dates and times:
1-5 March 2016
(Tue-Fri 20:00, Sat 19:00)
location:
Théâtre du Colibri
Eaux-Vives, Geneva
websites:
www.lspg.ch
www.scenesansfrontiere.ch
Technical Details:
Any font or combination of fonts is acceptable. The largest text should be the play title. The author's name must be at least 50% of the title font size.
For this competition, we would like the version with A3 proportions, which will also be used at F4 (89.5 x 128 cm) and A5 sizes (14.8 x 21 cm). Therefore no text should be below 9pt at A5.
However, from the winning designer we will also need repurposed sizes of the same design. Here is a comprehensive list of the sizes we will need.
1) A3 print poster. Artwork should be 300dpi, CMYK, sent with a 1mm bleed all round, to specification PDF/X-1A:2001. We will need this image in PDF format in addition to the default Artmarketo formats.
2) Chatterbook advert picture. 1200px by 628px, RGB jpeg. This must comply with Chatterbook’s restrictions on amount of text, which is no more than 20% of area taken up by text.(https://www.chatterbook-example.com/ads/tools/text_overlay).
Because of these restrictions it is sufficient to include just the title and the author's name in this version.
3) Chatterbook cover picture: 851px by 314px. RGB jpeg. It is sufficient to include just the title and the author's name in this version.
4) Web banner. 1000px by 300px. RGB jpeg. This version should include just the main image(s), no text.

```html
<!DOCTYPE html>
<html lang="en">
<head>
<meta charset="utf-8">
<title>Copper Lantern – Poster</title>
<link rel="stylesheet" href="https://fonts.googleapis.com/css2?family=Advent+Pro:wght@400&family=Open+Sans:wght@700&family=Open+Sans+Condensed:wght@700&display=swap">
<style>
  :root {
    --paper: #ffffff;
    --ink-violet: #6a64b8;
    --ring-dark: #45406a;
    --ring-mid: #5a56b0;
    --glow: #dffcf2;
    --title-red: #ff3b1c;
    --title-ghost: #f6a08e;
    --band-mint: #d8fbf3;
    --text-dark: #1c1c1c;
    --tag-light: #ffffff;
    --tag-lilac: #8a84e2;
  }
  html, body {
    margin: 0;
    padding: 0;
    overflow: hidden;
    background: var(--paper);
  }
  .poster {
    position: relative;
    width: 848px;
    height: 1200px;
    overflow: hidden;
    background: var(--paper);
  }
  .vortex-art {
    position: absolute;
    left: 0;
    top: 0;
    width: 848px;
    height: 1200px;
  }
  .presenter {
    position: absolute;
    top: 60px;
    right: 210px;
    margin: 0;
    text-align: right;
    font-family: "Open Sans Condensed", "Open Sans", sans-serif;
    font-weight: 700;
    font-size: 21px;
    line-height: 27px;
    color: var(--ink-violet);
  }
  .presenter-mark {
    position: absolute;
    top: 52px;
    right: 68px;
    width: 120px;
    height: 120px;
    border: 3px solid var(--ink-violet);
    border-radius: 50%;
    box-sizing: border-box;
  }
  .play-title {
    position: absolute;
    left: 0;
    top: 440px;
    width: 848px;
    height: 170px;
  }
  .play-title text {
    font-family: "Open Sans", Arial, sans-serif;
    font-weight: 700;
    font-size: 112px;
  }
  .tagline {
    position: absolute;
    left: 0;
    top: 607px;
    width: 848px;
    margin: 0;
    text-align: center;
    font-family: "Open Sans", sans-serif;
    font-weight: 700;
    font-size: 18px;
    letter-spacing: 0.2px;
    color: var(--tag-light);
  }
  .tagline .on-glow { color: var(--tag-lilac); }
  .credits, .details {
    position: absolute;
    margin: 0;
    padding: 0;
    list-style: none;
    font-family: "Advent Pro", sans-serif;
    color: var(--text-dark);
  }
  .credits { left: 0; top: 966px; }
  .credits .band {
    display: block;
    width: 452px;
    padding-left: 57px;
    box-sizing: border-box;
    font-size: 36px;
    line-height: 40px;
    margin-bottom: 14px;
    letter-spacing: 1px;
    background: linear-gradient(90deg, var(--band-mint) 70%, rgba(216,251,243,0));
  }
  .credits .web {
    display: block;
    padding-left: 63px;
    font-size: 22px;
    line-height: 28px;
    margin-bottom: 8px;
    letter-spacing: 1px;
    width: 300px;
    background: linear-gradient(90deg, var(--band-mint) 60%, rgba(216,251,243,0));
  }
  .details { right: 6px; top: 960px; text-align: right; }
  .details li {
    display: block;
    width: 330px;
    padding-right: 57px;
    font-size: 23px;
    line-height: 28px;
    margin-bottom: 8px;
    letter-spacing: 1px;
    background: linear-gradient(270deg, var(--band-mint) 75%, rgba(216,251,243,0));
  }
</style>
</head>
<body>
<main class="poster">
  <svg class="vortex-art" viewBox="0 0 848 1200" role="img" aria-label="Abstract painted swirl: a dark violet ring spiralling around a glowing pale mint centre">
    <defs>
      <radialGradient id="glowFill" cx="50%" cy="50%" r="50%">
        <stop offset="0%" stop-color="#ffffff"/>
        <stop offset="45%" stop-color="#e6fdf6"/>
        <stop offset="80%" stop-color="#c9f6ec"/>
        <stop offset="100%" stop-color="#b8c4f0"/>
      </radialGradient>
      <filter id="softWide"><feGaussianBlur stdDeviation="22"/></filter>
      <filter id="softMid"><feGaussianBlur stdDeviation="16"/></filter>
    </defs>
    <ellipse cx="440" cy="530" rx="410" ry="405" fill="var(--ring-dark)" filter="url(#softWide)"/>
    <ellipse cx="395" cy="560" rx="265" ry="255" fill="var(--ring-mid)" filter="url(#softMid)"/>
    <ellipse cx="375" cy="560" rx="205" ry="195" fill="url(#glowFill)" filter="url(#softMid)"/>
  </svg>

  <p class="presenter">Lakeside Stage<br>Players Guild<br>presents</p>
  <span class="presenter-mark" aria-hidden="true"></span>

  <svg class="play-title" viewBox="0 0 848 170" role="heading" aria-level="1" aria-label="Copper Lantern">
    <text x="36" y="104" fill="var(--title-ghost)" opacity="0.7" textLength="760" lengthAdjust="spacingAndGlyphs">Copper Lantern.</text>
    <text x="44" y="148" fill="var(--title-ghost)" opacity="0.55" textLength="760" lengthAdjust="spacingAndGlyphs">Copper Lantern.</text>
    <text x="50" y="130" fill="var(--title-red)" textLength="745" lengthAdjust="spacingAndGlyphs">Copper Lantern.</text>
  </svg>

  <p class="tagline">How do yo<span class="on-glow">u keep it together when your whole wor</span>ld's fallen apart?</p>

  <ul class="credits">
    <li class="band">by Martin Crowe-Fenwick</li>
    <li class="band">directed by Ned Pilbury</li>
    <li class="web">www.scenesansfrontiere.ch</li>
    <li class="web">www.lspg.ch</li>
  </ul>

  <ul class="details">
    <li>1-5 March 2016</li>
    <li>(Tue-Fri 20:00, Sat 19:00)</li>
    <li>Théâtre du Colibri</li>
    <li>Eaux-Vives, Geneva</li>
  </ul>
</main>
</body>
</html>
```